Business card for law firm

Need business card for new law firm. Think confident, authoritative, conservative, but not stuffy or old-fashioned.

Contact Information for Business Card

Content for card - logo (uploaded), plus the following:

Paul Whitcombe (larger font)
Managing Partner (larger font, but not as large as name)
Level 9, 7 Ferris Lane
Sydney NSW 2000
Main Tel 02 9364 2710
Direct Tel 02 8472 3159
Email paul@qvlegal.com.au
www.qvlegal.com.au

Letterhead design should include logo plus:
Level 9, 7 Ferris Lane
Sydney NSW 2000
Tel 02 8472 3159
www.qvlegal.com.au

```html
<!DOCTYPE html>
<html lang="en">
<head>
<meta charset="utf-8">
<title>Quayvale Legal – Business Card</title>
<link rel="stylesheet" href="https://fonts.googleapis.com/css2?family=Source+Sans+3:wght@400;600;700&display=swap">
<style>
  :root {
    --navy: #0b1d57;
    --navy-deep: #001a52;
    --ink: #111111;
    --grey: #6a6a6a;
    --rule: #c9c9c9;
    --paper: #ffffff;
    --backdrop: #dcdcdc;
  }
  * { margin: 0; padding: 0; box-sizing: border-box; }
  html, body {
    width: 1125px;
    height: 1200px;
    overflow: hidden;
    background: var(--backdrop);
    font-family: "Source Sans 3", "Myriad Pro", Arial, sans-serif;
  }
  .card {
    position: absolute;
    left: 150px;
    width: 824px;
    height: 471px;
    overflow: hidden;
  }
  .card--front { top: 98px; background: var(--paper); }
  .card--back { top: 630px; background: var(--navy-deep); }

  /* Front: brand block */
  .brand {
    position: absolute;
    left: 60px;
    top: 110px;
    width: 340px;
    text-align: center;
    color: var(--navy);
    font-weight: 600;
  }
  .brand__mark {
    display: block;
    width: 64px;
    height: 64px;
    margin: 0 auto 28px;
    background: var(--navy);
  }
  .brand__name {
    display: block;
    font-size: 46px;
    letter-spacing: 3px;
    line-height: 1;
  }
  .brand__sub {
    display: block;
    margin-top: 14px;
    font-size: 17px;
    letter-spacing: 17px;
    padding-left: 17px;
    line-height: 1;
  }

  .divider {
    position: absolute;
    left: 456px;
    top: 103px;
    width: 1px;
    height: 244px;
    background: var(--rule);
  }

  /* Front: contact block */
  .contact {
    position: absolute;
    left: 495px;
    top: 112px;
    color: var(--grey);
  }
  .contact__name {
    font-size: 29px;
    font-weight: 700;
    color: var(--navy);
    line-height: 1.1;
  }
  .contact__title {
    font-size: 20px;
    font-weight: 700;
    line-height: 1.1;
    margin-top: 1px;
  }
  .contact__address {
    margin-top: 17px;
    font-size: 20px;
    line-height: 27px;
  }
  .contact__lines {
    list-style: none;
    margin-top: 16px;
    font-size: 20px;
    line-height: 27px;
  }
  .contact__lines li {
    display: flex;
    align-items: center;
  }
  .contact__icon {
    width: 22px;
    height: 20px;
    margin-right: 14px;
    margin-left: -5px;
    fill: var(--navy);
    flex: none;
  }

  /* Front: web band */
  .web-band {
    position: absolute;
    left: 0;
    top: 402px;
    width: 673px;
    height: 40px;
    background: var(--navy);
    color: var(--paper);
    font-size: 20px;
    letter-spacing: 15px;
    line-height: 40px;
    padding-left: 143px;
  }
  .web-band__tab {
    position: absolute;
    top: 402px;
    left: 673px;
    width: 34px;
    height: 40px;
    background: var(--navy);
    border-left: 3px solid var(--paper);
  }
  .web-band__end {
    position: absolute;
    top: 402px;
    left: 707px;
    width: 117px;
    height: 40px;
    background: #000;
  }

  /* Back */
  .back-brand {
    position: absolute;
    inset: 0;
    display: flex;
    flex-direction: column;
    align-items: center;
    justify-content: center;
    color: var(--paper);
    font-weight: 600;
    text-align: center;
  }
  .back-brand__mark {
    width: 96px;
    height: 96px;
    background: var(--paper);
    margin-bottom: 36px;
  }
  .back-brand__name {
    font-size: 56px;
    letter-spacing: 4px;
    line-height: 1;
  }
  .back-brand__sub {
    margin-top: 16px;
    font-size: 20px;
    letter-spacing: 20px;
    padding-left: 20px;
    line-height: 1;
  }
</style>
</head>
<body>

<section class="card card--front">
  <div class="brand">
    <span class="brand__mark"></span>
    <span class="brand__name">QUAYVALE</span>
    <span class="brand__sub">LEGAL</span>
  </div>

  <div class="divider"></div>

  <div class="contact">
    <p class="contact__name">PAUL WHITCOMBE</p>
    <p class="contact__title">MANAGING PARTNER</p>
    <p class="contact__address">Level 9, 7 Ferris Lane<br>Sydney NSW 2000</p>
    <ul class="contact__lines">
      <li>
        <svg class="contact__icon" viewBox="0 0 22 20" aria-hidden="true">
          <path d="M1 6c0-3 4-5 10-5s10 2 10 5v2h-5V6c-2-1-8-1-10 0v2H1z"/>
          <path d="M5 9h12l2 9H3z"/>
          <circle cx="11" cy="13" r="2.6" fill="#fff"/>
        </svg>
        02 9364 2710
      </li>
      <li>
        <svg class="contact__icon" viewBox="0 0 22 20" aria-hidden="true">
          <rect x="6" y="0" width="10" height="20" rx="2"/>
          <rect x="8" y="3" width="6" height="11" fill="#fff"/>
          <circle cx="11" cy="17" r="1.2" fill="#fff"/>
        </svg>
        02 8472 3159
      </li>
      <li>
        <svg class="contact__icon" viewBox="0 0 22 20" aria-hidden="true">
          <rect x="1" y="5" width="18" height="11"/>
          <path d="M1 5l9 6 9-6" fill="none" stroke="#fff" stroke-width="1.6"/>
        </svg>
        paul@qvlegal.com.au
      </li>
    </ul>
  </div>

  <div class="web-band">www.qvlegal.com.au</div>
  <div class="web-band__tab"></div>
  <div class="web-band__end"></div>
</section>

<section class="card card--back">
  <div class="back-brand">
    <span class="back-brand__mark"></span>
    <span class="back-brand__name">QUAYVALE</span>
    <span class="back-brand__sub">LEGAL</span>
  </div>
</section>

</body>
</html>
```